Institutional website for an IT Consulting company

Web design + HTML + CSS / Bootstrap + JS (interaction) integration in order to extend our existing website brightvale.coop.
Our website is currently aiming only for recruitment and not for customers, we want to provide a fluid transition between customer side website (this project) and recruitment website (existing site).

Ideally we would love the new design to be "inspired" by our actual graphic chart (Colors mainly). It should provide a great user experience and a landing page (or any mean) allowing the visitor to easily switch from the end customer front end (this project), the recruitment front end (existing front end https://www.brightvale.coop/) and the existing member front end (an other existing front end dedicated to members already existing).

In attachment you will find the expected site content mainly a one page with a first level of information and "link" to sub pages (a way to directly access this sub pages should also be provided).

The website should be accessible on mobile device and desktop.

The attachment is in french as it reflect the final site content, but if google translate isn't sufficient to have a general idea of the content, feel free to ask. We would love to have some visual representation for some categories.

Target Market(s)

fortune 500 companies

Industry/Entity Type

It Company

Coding

Coded - Design and coding required

Number of Pages Required

5+ page

Requirements
Must have
• This project must have an easy way to navigate between 3 sub sites, the customer one (the one designed here), the consultant / recruitment one (the existing one at brightvale.coop), the members one.

A one page experience at first leading to detail pages.

Custom made visuals to illustrate each categories.

Inspiration websites : pirog[.]fr ; tasklynn[.]com ; dorvelo[.] com ...

Be inspired by the existing color from our logo and existing website at brightvale[.]coop

```html
<!DOCTYPE html>
<html lang="en">
<head>
<meta charset="utf-8">
<title>Brightvale.coop – Why use an AEC-COPA?</title>
<link rel="stylesheet" href="https://fonts.googleapis.com/css2?family=Montserrat:wght@400;500;600;700&family=Lato:ital,wght@0,400;0,700;1,400&display=swap">
<style>
:root{
  --teal:#14afb8;
  --teal-dark:#0f9aa3;
  --ink:#2b2b2b;
  --brand-dark:#0d3b3e;
  --body:#7b7b7b;
  --line:#d9d9d9;
  --white:#ffffff;
}
*{box-sizing:border-box;margin:0;padding:0}
html,body{width:1200px;height:3700px;overflow:hidden;background:var(--white)}
body{position:relative;font-family:"Lato",sans-serif;color:var(--body)}
.abs{position:absolute}
h1,h2,h3,h4,.brand,.btn{font-family:"Montserrat",sans-serif}

/* header */
.brand{display:flex;align-items:center;gap:10px;font-weight:700;color:var(--brand-dark);letter-spacing:1px}
.brand .mark{width:18px;height:18px;background:var(--teal)}
.site-header .brand{left:110px;top:32px;font-size:40px}
.utility{right:112px;top:16px;font-family:"Montserrat",sans-serif;font-size:14px;font-weight:500;color:var(--ink);display:flex;gap:12px;align-items:center}
.utility svg{vertical-align:-2px;margin-right:4px}
.nav{top:49px;right:112px;display:flex;gap:17px}
.btn{display:inline-block;height:50px;line-height:46px;padding:0 14px;border:2px solid #aaa;font-size:15px;font-weight:600;color:#555;text-transform:uppercase}
.btn.dark{background:var(--ink);border-color:var(--ink);color:var(--white)}

/* hero */
.hero{left:0;top:122px;width:1200px;height:405px;background:linear-gradient(90deg,#f2f2f2 0%,#e6e6e6 45%,#b9b5ae 75%,#5b5e66 100%)}
.hero h1{position:absolute;left:112px;top:100px;color:var(--ink);line-height:1.15}
.hero h1 .small{display:block;font-size:52px;font-weight:500;letter-spacing:1px}
.hero h1 .big{display:block;font-size:70px;font-weight:700}
.dots{position:absolute;left:550px;top:344px;display:flex;gap:12px}
.dots span{width:17px;height:17px;border-radius:50%;border:2px solid #555}
.dots span.on{background:#555}

/* feature circles */
.disc{width:394px;height:394px;border-radius:50%;background:var(--white);box-shadow:0 6px 22px rgba(0,0,0,.13);display:flex;align-items:center;justify-content:center}
.disc .art{width:240px;height:240px;border-radius:50%;background:radial-gradient(circle,#d6f0f2 0%,#eef6f7 60%,#fff 100%)}

.copy h2{font-size:26px;font-weight:500;color:#333;margin-bottom:14px}
.copy h3{font-size:26px;font-weight:500;color:#333;margin:26px 0 14px}
.copy p{font-size:14.5px;line-height:27.5px;margin-bottom:27px}
.copy p.tight{margin-bottom:0}
.copy .title{font-size:44px;font-weight:700;color:var(--ink);line-height:1.35;text-transform:uppercase;margin-bottom:18px}
.copy .lead{font-family:"Montserrat",sans-serif;font-size:19px;line-height:31px;color:#444;margin-bottom:8px}

/* testimonials */
.testimonials{left:0;top:2774px;width:1200px;height:510px;background:linear-gradient(90deg,var(--teal) 0%,#17b3bc 60%,#12a9b2 100%)}
.testimonials h2{position:absolute;top:52px;width:100%;text-align:center;color:var(--white);font-size:44px;font-weight:700}
.clients{position:absolute;left:110px;top:169px;display:flex;gap:16px}
.client{width:183px;height:87px;border:5px solid rgba(255,255,255,.45);display:flex;align-items:center;justify-content:center;font-family:"Montserrat",sans-serif;font-weight:700;font-size:30px;color:rgba(255,255,255,.55);letter-spacing:1px}
.client.active{border-color:var(--white);color:var(--white);letter-spacing:6px}
.arrow{position:absolute;top:198px}
.divider{position:absolute;left:110px;top:311px;width:980px;height:1px;background:rgba(255,255,255,.35)}
.avatar{position:absolute;left:108px;top:326px;width:120px;height:120px;border-radius:50%;background:linear-gradient(160deg,#f4f4f4,#c9c3bb)}
.person{position:absolute;left:257px;top:358px;color:var(--white);font-size:19px;line-height:31px}
.quote{position:absolute;left:385px;top:344px;width:700px;color:var(--white);font-style:italic;font-size:16px;line-height:27.5px}

/* footer */
.site-footer .brand{left:110px;top:3418px;font-size:40px}
.fcol h4{font-size:19px;font-weight:500;color:#333;margin-bottom:10px}
.fcol li{list-style:none;font-size:14.5px;line-height:26.5px;color:#777}
.contact li{display:flex;gap:8px;margin-bottom:26px;line-height:26px}
.contact svg{flex:none;margin-top:6px}
.rule{left:110px;top:3612px;width:980px;height:1px;background:var(--line)}
.copyright{left:110px;top:3647px;font-size:14.5px;color:#777}
.social{left:946px;top:3634px;display:flex;gap:6px}
.social span{width:43px;height:43px;border-radius:50%;border:1.5px solid var(--teal)}
</style>
</head>
<body>

<header class="site-header">
  <div class="brand abs"><span>BRIGHTVALE</span><span class="mark"></span></div>
  <div class="utility abs">
    <span><svg width="10" height="12" viewBox="0 0 10 12"><rect x="1" y="5" width="8" height="7" rx="1" fill="#14afb8"/><path d="M3 5V3.5a2 2 0 0 1 4 0V5" stroke="#14afb8" stroke-width="1.6" fill="none"/></svg>LOG IN</span>
    <span>|</span>
    <span><svg width="13" height="13" viewBox="0 0 13 13"><circle cx="6.5" cy="6.5" r="6.5" fill="#14afb8"/><text x="6.5" y="10" font-size="9" font-family="Arial,sans-serif" font-weight="700" fill="#fff" text-anchor="middle">?</text></svg>HELP</span>
  </div>
  <nav class="nav abs">
    <a class="btn">I am Brightvale</a>
    <a class="btn">I wish to join Brightvale</a>
    <a class="btn dark">Contact us</a>
  </nav>
</header>

<section class="hero abs" role="img" aria-label="Smiling consultant in glasses at his desk">
  <h1><span class="small">WHY USE A</span><span class="big">AEC-COPA?</span></h1>
  <div class="dots"><span class="on"></span><span></span><span></span><span></span></div>
</section>

<section>
  <div class="disc abs" style="left:111px;top:606px"><div class="art" role="img" aria-label="Laptop with pencil icon"></div></div>
  <div class="copy abs" style="left:575px;top:628px;width:530px">
    <h2>What is a AEC-COPA?</h2>
    <p>Brightvale is an activity and employment cooperative which has the legal status of a cooperative and participatory association (SCOP in French). Do these words seem fuzzy to you? Here is an explanation that will allow you to understand how we operate:</p>
    <p>An AEC like Brightvale gathers a group of consultant who wish to develop their own entrepreneur activity whilst being part of a collective company and benefiting from the salaried status.<br>We chose the legal status of COPA so that each of our S/E can work on their professional activity whilst having the opportunity to profit from the contributors' experiences in their area. Because of this status, we adopted a democratic governance: all decision-making are taken by vote of the associated S/E. The S∫E can become associated by simple request and have an obligation to become one after 3 years of service.</p>
    <p class="tight">Regarding the stewardship, it is a volunteer work that lasts for only 3 years and is available to all our S/E and has to be voted by all the S/E.</p>
    <h3>A dual role: Entrepreneur and salaried?</h3>
    <p>Our consultant have a status of S∫E in our COPA, a dual role that allows them to work directly with you in total autonomy whilst enjoying the benefits of being salaried: training account, paid vacation, health mutual etc.</p>
    <p class="tight">All our consultants have different profiles with different area of expertise that will meet your requirement in the data area.</p>
    <h3>Custom-made?</h3>
    <p class="tight">Our team is composed of different profiles who all have the same interest regarding data technologies with a specialization on Cloudmere tools. From junior to senior S∫E, from development to advising and training or audit, we will be able to adapt to your needs.</p>
  </div>
</section>

<section>
  <div class="copy abs" style="left:108px;top:1638px;width:540px">
    <div class="title">A collective at<br>your service</div>
    <p class="lead">Choosing a service delivery with Brightvale is working with a community, not a self-employed worker:</p>
    <h3 style="margin-top:12px">A support department at your disposal</h3>
    <p class="tight">A sales team is available to answer to all of your questions, whether their concern the way we operate our organisation or your research of service. Procedure simplified allowing agility in contracts.</p>
    <h3 style="margin-top:14px">Mutual help in our community</h3>
    <p class="tight">Mutual help is significant to us. It allows us to compare our ideas and to strengthen our skills to offer you the best possible service.</p>
    <h3 style="margin-top:14px">Shared technology watch</h3>
    <p class="tight">We keep up to date an internal tool where everyone can share the latest news on tools we use. We also set up meetings targeted at an expert or user audience about the use of technological tools or feedback on our experiences.</p>
  </div>
  <div class="disc abs" style="left:691px;top:1643px"><div class="art" role="img" aria-label="Headset surrounded by arrows icon"></div></div>
</section>

<section>
  <div class="disc abs" style="left:111px;top:2305px"><div class="art" role="img" aria-label="Invoice with dollar sign icon"></div></div>
  <div class="copy abs" style="left:575px;top:2330px;width:520px">
    <div class="title" style="margin-bottom:20px">A fair pay</div>
    <p>Each invoice we make on behalf of Brightvale.coop is directly paid to the S/E. A fixed share is dedicated to the functioning of the commercial and administrative service. Nothing is simpler.</p>
    <p class="tight">Within Brightvale, everyone is responsible of its own wage according to its sales revenue. The S∫E owns an analytical account he or she can manage and check at all times in order to track revenues and expenses throughout the year.</p>
  </div>
</section>

<section class="testimonials abs">
  <h2>CLIENT TESTIMONIALS</h2>
  <svg class="arrow" style="left:66px" width="16" height="30" viewBox="0 0 16 30"><path d="M14 2 2 15l12 13" stroke="#fff" stroke-width="2.5" fill="none"/></svg>
  <div class="clients">
    <div class="client">NORTHLY</div>
    <div class="client">NORTHLY</div>
    <div class="client active">VELKA</div>
    <div class="client">NORTHLY</div>
    <div class="client">NORTHLY</div>
  </div>
  <svg class="arrow" style="left:1104px" width="16" height="30" viewBox="0 0 16 30"><path d="M2 2l12 13L2 28" stroke="#fff" stroke-width="2.5" fill="none"/></svg>
  <div class="divider"></div>
  <div class="avatar" role="img" aria-label="Portrait of the client"></div>
  <div class="person">Alex Marlow<br>CEO</div>
  <p class="quote">“Nam libero tempore, cum soluta nobis est eligendi opticum que nihil impedit quo minus id quod maxime placeat facere possimus, omnis voluptas assumenda est, omnis dolor rep ellendu autem quibusdam et aut .”</p>
</section>

<footer class="site-footer">
  <div class="brand abs"><span>BRIGHTVALE</span><span class="mark"></span></div>
  <div class="fcol abs" style="left:468px;top:3332px">
    <h4>Information</h4>
    <ul><li>About us</li><li>Team</li><li>Jobs</li><li>Hurry</li><li>Freelancing news</li><li>Data protection</li><li>Help</li><li>Sitemap</li></ul>
  </div>
  <div class="fcol abs" style="left:674px;top:3332px">
    <h4>Quick Links</h4>
    <ul><li>Offers and prices</li><li>Company</li><li>Open Brightvale coop</li><li>Insights</li><li>Create my Profile</li></ul>
  </div>
  <div class="fcol contact abs" style="left:880px;top:3332px">
    <h4>Find Us</h4>
    <ul>
      <li><svg width="10" height="14" viewBox="0 0 10 14"><path d="M5 0a5 5 0 0 1 5 5c0 4-5 9-5 9S0 9 0 5a5 5 0 0 1 5-5z" fill="#14afb8"/><circle cx="5" cy="5" r="2" fill="#fff"/></svg><span>24 Rue des Lilas<br>75011 Paris</span></li>
      <li><svg width="13" height="13" viewBox="0 0 13 13"><path d="M3 0l2 3-1.5 1.5a8 8 0 0 0 5 5L10 8l3 2-1.5 2.5C6 13 0 7 .5 1.5z" fill="#14afb8"/></svg><span>01 45 67 20 13</span></li>
      <li><svg width="15" height="11" viewBox="0 0 15 11"><rect width="15" height="11" rx="1" fill="#14afb8"/><path d="M1 1l6.5 5L14 1" stroke="#fff" stroke-width="1.3" fill="none"/></svg><span>contact@brightvale.coop</span></li>
    </ul>
  </div>
  <div class="rule abs"></div>
  <div class="copyright abs">© 2020, Brightvale.coop.</div>
  <div class="social abs" aria-label="Social networks"><span></span><span></span><span></span></div>
</footer>

</body>
</html>
```